Mara Penrith Copywriter Website

I am starting a new business as a freelance copywriter. Trying to set up the website for my business is proving to be too technical for me. I would like a simple, clean website using primarily black and white. I have attached the logo I would like used. I would like the menu icons to be Home, Services, Portfolio, Blog, Contact. I would like my mobile phone number (0412 583 906) and email address (mara.penrith.copywriter@fernmail.test) used in the header of the site. I need the site to be easily manageable and inter-changeable for me to be able to move things around and add images, etc with ease.

I would like the home page to be a static page with space for an image of myself somewhere (I haven't had this taken as yet), an area to put a bit about myself and my business, and also somewhere to include social media icons/links. Again, I would like the whole website and home page to be easily managed so that I can add/delete things with ease.

I would like the image of the typewriter used in the website somewhere also please.

Coding

Coded - Design and coding required

Number of Pages Required

5+ page

Font styles to use
Sans Serif
Script

Colors
fdf0f6

Requirements
Must have
• The logo provided
• Ability to change page contents easily
• Ability to add social media icons as needed
Nice to have
• Use of the typewriter image
Should not have
• Complicated pages that are not easily editable

```html
<!DOCTYPE html>
<html lang="en">
<head>
<meta charset="utf-8">
<title>Mara Penrith Copywriter</title>
<link href="https://fonts.googleapis.com/css2?family=Montserrat:wght@600;700&family=Roboto:wght@400;500;700&family=Open+Sans:wght@400;700&family=Lato:wght@400;700&display=swap" rel="stylesheet">
<style>
:root{
  --black:#000;
  --ink:#111;
  --white:#fff;
  --pink:#f8e9ea;
  --pink-ring:#f6e3e5;
  --grey:#777;
  --footer:#141414;
  --footer-text:#cfcfcf;
}
*{margin:0;padding:0;box-sizing:border-box}
html,body{width:1200px;height:3495px;overflow:hidden}
body{position:relative;background:var(--white);font-family:"Lato",sans-serif;color:var(--ink)}
.abs{position:absolute}

/* social link buttons (generic share / link / chat glyphs) */
.social-link{display:flex;align-items:center;justify-content:center;border-radius:50%}
.social-link svg{display:block}

/* top bar */
.topbar{left:0;top:0;width:1200px;height:42px;background:var(--black);color:var(--white)}
.topbar .social{left:86px;top:10px;display:flex;gap:20px}
.topbar .social-link{width:22px;height:22px;background:var(--white)}
.topbar .social-link svg{width:14px;height:14px}
.topbar .contact{right:64px;top:8px;display:flex;gap:26px;font-size:15px;align-items:center}
.topbar .contact span{display:flex;align-items:center;gap:8px}
.topbar .contact svg{width:26px;height:26px}
.topbar .phone{font-weight:700}

/* nav */
.header{left:0;top:42px;width:1200px;height:93px;background:var(--white)}
.brand{left:77px;top:22px;display:flex;align-items:center;gap:12px;font-family:"Montserrat",sans-serif;font-weight:600;font-size:24px;color:var(--ink)}
.brand .mark{width:18px;height:18px;background:var(--pink-ring)}
.brand small{display:block;font-size:13px;letter-spacing:4px;color:var(--ink);font-weight:600}
.nav{right:77px;top:24px;display:flex;font-family:"Roboto",sans-serif;font-size:16px;text-transform:uppercase}
.nav a{display:block;padding:13px 17px;color:var(--ink);text-decoration:none}
.nav a.active{background:var(--black);color:var(--white);padding:13px 22px}

/* hero */
.hero{left:0;top:135px;width:1200px;height:543px;background:linear-gradient(100deg,#e9e7e4 0%,#d8d5d0 40%,#b9b3ab 70%,#8d857c 100%)}
.hero h1{left:77px;top:132px;font-family:"Montserrat",sans-serif;font-weight:700;font-size:57px;line-height:66px;color:var(--white);text-shadow:0 2px 6px rgba(0,0,0,.25)}
.btn{display:flex;align-items:center;justify-content:center;gap:12px;background:var(--black);color:var(--white);font-family:"Roboto",sans-serif;font-weight:700;font-size:21px;text-transform:uppercase}
.btn svg{width:32px;height:32px}
.hero .btn{left:77px;top:357px;width:228px;height:63px}
.arrow-btn{top:256px;width:50px;height:50px;border-radius:50%;background:rgba(0,0,0,.45);display:flex;align-items:center;justify-content:center}
.arrow-btn svg{width:20px;height:20px}

/* welcome */
.section-title{left:0;width:1200px;text-align:center;font-family:"Roboto",sans-serif;font-weight:500;font-size:40px;text-transform:uppercase;color:var(--ink)}
.lede{left:200px;width:800px;text-align:center;font-size:13px;line-height:25px;color:var(--grey)}
.ring{left:286px;top:874px;width:628px;height:628px;border-radius:50%;background:var(--pink-ring)}
.ring-inner{left:357px;top:945px;width:486px;height:486px;border-radius:50%;background:var(--white)}
.ring-line{left:378px;top:966px;width:444px;height:444px;border-radius:50%;border:1px solid #f1dadd}
.typewriter{left:431px;top:1037px;width:333px;height:443px;background:linear-gradient(180deg,#f2f2f2 0%,#e4e4e4 28%,#2a2a2a 34%,#111 70%,#3a3a3a 100%);border-radius:6px}

/* services */
.services{left:0;top:1382px;width:1200px;height:618px;background:var(--pink)}
.services h2{font-family:"Open Sans",sans-serif;font-weight:700;font-size:40px;top:124px}
.service{top:222px;width:250px;text-align:center}
.service .icon{width:112px;height:112px;margin:0 auto;border-radius:50%;background:var(--white);box-shadow:0 6px 10px rgba(0,0,0,.08);display:flex;align-items:center;justify-content:center}
.service .icon svg{width:60px;height:60px}
.service h3{margin-top:34px;font-family:"Roboto",sans-serif;font-weight:700;font-size:21px}
.service p{margin-top:12px;font-size:13px;line-height:24px;color:var(--grey)}
.services .btn{left:506px;top:496px;width:188px;height:58px}

/* projects */
.projects-sub{top:2117px}
.grid{left:0;top:2183px;width:1200px;height:462px;display:grid;grid-template-columns:repeat(4,300px);grid-template-rows:repeat(2,231px)}
.tile:nth-child(1){background:linear-gradient(135deg,#c9d7da,#7e9aa1)}
.tile:nth-child(2){background:linear-gradient(135deg,#b6c7d3,#7d6f63)}
.tile:nth-child(3){background:linear-gradient(135deg,#6a4f39,#3c2a1d)}
.tile:nth-child(4){background:linear-gradient(135deg,#2a3240,#7b6e8a)}
.tile:nth-child(5){background:linear-gradient(135deg,#4a4540,#c9b49a)}
.tile:nth-child(6){background:linear-gradient(135deg,#56606b,#8a939c)}
.tile:nth-child(7){background:linear-gradient(135deg,#1c1c1c,#3e3e3e)}
.tile:nth-child(8){background:linear-gradient(135deg,#d8d2cb,#8d8077)}
.viewall-band{left:0;top:2645px;width:1200px;height:93px;background:var(--black)}
.viewall-band .btn{width:100%;height:100%;background:none}

/* blog */
.post{top:2880px;width:500px;height:238px}
.post .thumb{left:0;top:0;width:221px;height:238px}
.post .date{left:179px;top:28px;width:59px;height:61px;background:var(--black);color:var(--white);text-align:center;font-family:"Roboto",sans-serif}
.post .date b{display:block;font-size:27px;line-height:36px}
.post .date small{font-size:12px}
.post .body{left:252px;top:32px;width:240px}
.post h4{font-family:"Roboto",sans-serif;font-weight:700;font-size:18px;line-height:26px}
.post p{margin-top:22px;font-size:12.5px;line-height:25px;color:var(--grey)}
.post .more{margin-top:10px;display:inline-block;font-size:12.5px;font-weight:700;font-style:italic;color:var(--ink);text-decoration:underline}

/* footer */
.footer{left:0;top:3185px;width:1200px;height:245px;background:var(--footer);color:var(--footer-text)}
.footer .brand{left:77px;top:82px;color:var(--white)}
.footer .brand small{color:var(--white)}
.footer .social{left:122px;top:143px;display:flex;gap:10px}
.footer .social-link{width:44px;height:44px;background:var(--white)}
.footer .social-link svg{width:22px;height:22px}
.footer h5{font-family:"Roboto",sans-serif;font-weight:700;font-size:18px;color:var(--white);text-transform:uppercase}
.col{top:44px}
.sitemap ul{list-style:none;margin-top:18px}
.sitemap li{font-size:13px;line-height:29px}
.sitemap li::before{content:"";display:inline-block;width:5px;height:5px;border-radius:50%;background:var(--footer-text);margin-right:12px;vertical-align:middle}
.contact-list{margin-top:22px}
.contact-list div{display:flex;gap:14px;font-size:13px;line-height:22px;margin-bottom:14px;width:200px}
.contact-list svg{width:18px;height:18px;flex:none;margin-top:2px}
.newsletter p{margin-top:16px;font-size:13px;line-height:22px;width:250px}
.subscribe{margin-top:14px;display:flex;width:250px;height:42px}
.subscribe span{flex:1;background:var(--white);color:#888;font-size:11px;padding:14px 14px}
.subscribe b{width:42px;background:#9a9a9a;display:flex;align-items:center;justify-content:center}
.subscribe svg{width:20px;height:20px}
.copyright{left:0;top:3430px;width:1200px;height:65px;background:var(--black);color:var(--white);text-align:center;font-size:14px;line-height:65px}
</style>
</head>
<body>

<div class="abs topbar">
  <div class="abs social">
    <a class="social-link" aria-label="Share"><svg viewBox="0 0 20 20"><circle cx="5" cy="10" r="2.6" fill="#000"/><circle cx="15" cy="4.5" r="2.6" fill="#000"/><circle cx="15" cy="15.5" r="2.6" fill="#000"/><path d="M5 10l10-5.5M5 10l10 5.5" stroke="#000" stroke-width="1.8"/></svg></a>
    <a class="social-link" aria-label="Link"><svg viewBox="0 0 20 20"><rect x="1.5" y="7" width="10" height="6" rx="3" fill="none" stroke="#000" stroke-width="2"/><rect x="8.5" y="7" width="10" height="6" rx="3" fill="none" stroke="#000" stroke-width="2"/></svg></a>
    <a class="social-link" aria-label="Message"><svg viewBox="0 0 20 20"><path d="M3 4h14v9H8l-4 3v-3H3z" fill="#000"/></svg></a>
  </div>
  <div class="abs contact">
    <span class="phone"><svg viewBox="0 0 26 26"><circle cx="13" cy="13" r="13" fill="#fff"/><path d="M9 7l3 3-2 2c1 2 3 4 5 5l2-2 3 3-2 2c-5 0-11-6-11-11z" fill="#000"/></svg>0412 583 906</span>
    <span><svg viewBox="0 0 26 26"><circle cx="13" cy="13" r="13" fill="#fff"/><rect x="7" y="9" width="12" height="8" fill="#000"/><path d="M7 9l6 5 6-5" stroke="#fff" fill="none"/></svg>mara.penrith.copywriter@fernmail.test</span>
  </div>
</div>

<header class="abs header">
  <div class="abs brand"><i class="mark"></i><div>Mara Penrith<small>COPYWRITER</small></div></div>
  <nav class="abs nav">
    <a class="active">Home</a><a>Services</a><a>Portfolio</a><a>Blog</a><a>Contact</a>
  </nav>
</header>

<section class="abs hero" role="img" aria-label="Photo of a copywriter at a bright home-office desk with a lamp and laptop">
  <h1 class="abs">Ready To<br>Freelance As A<br>Copywriter?</h1>
  <div class="abs btn">Get Started <svg viewBox="0 0 32 32"><circle cx="16" cy="16" r="13" fill="none" stroke="#fff" stroke-width="2.5"/><path d="M11 16h10M17 11l5 5-5 5" fill="none" stroke="#fff" stroke-width="2.5"/></svg></div>
  <div class="abs arrow-btn" style="left:12px"><svg viewBox="0 0 20 20"><path d="M13 3l-7 7 7 7" stroke="#fff" stroke-width="2" fill="none"/></svg></div>
  <div class="abs arrow-btn" style="right:12px"><svg viewBox="0 0 20 20"><path d="M7 3l7 7-7 7" stroke="#fff" stroke-width="2" fill="none"/></svg></div>
</section>

<h2 class="abs section-title" style="top:736px">Welcome to Mara Penrith</h2>
<p class="abs lede" style="top:800px">Lorem Ipsum is simply dummy text of the printing and typesetting industry. Lorem Ipsum has been the industry's standard dummy text ever since the 1500s, when an unknown printer took a galley of type and scrambled it to make a type specimen book. It has survived not only five centuries, but also the leap into electronic typesetting.</p>

<section class="abs services">
  <h2 class="abs section-title">Services We Provide You</h2>
  <div class="abs service" style="left:73px">
    <div class="icon"><svg viewBox="0 0 52 52"><rect x="8" y="11" width="36" height="30" fill="none" stroke="#000" stroke-width="3"/><path d="M8 18h36" stroke="#000" stroke-width="3"/><rect x="13" y="23" width="10" height="13" fill="#000"/><path d="M27 24h12M27 30h12M27 35h8" stroke="#000" stroke-width="2.5"/></svg></div>
    <h3>APP</h3><p>Lorem Ipsum is simply dummy text of the printing and typesetting industry. Ipsum has been.</p>
  </div>
  <div class="abs service" style="left:339px">
    <div class="icon"><svg viewBox="0 0 52 52"><rect x="17" y="10" width="18" height="12" fill="#000"/><rect x="11" y="21" width="30" height="3" fill="#000"/><path d="M14 32l10 4-10 4zM38 32l-10 4 10 4z" fill="#000"/><circle cx="26" cy="36" r="2.5" fill="#000"/></svg></div>
    <h3>BRAND</h3><p>Lorem Ipsum is simply dummy text of the printing and typesetting industry. Ipsum has been.</p>
  </div>
  <div class="abs service" style="left:604px">
    <div class="icon"><svg viewBox="0 0 52 52"><circle cx="26" cy="26" r="11" fill="#000"/><path d="M26 5v6M26 41v6M5 26h6M41 26h6M11 11l4 4M37 37l4 4M41 11l-4 4M11 41l4-4" stroke="#000" stroke-width="2.5"/></svg></div>
    <h3>SOCIAL</h3><p>Lorem Ipsum is simply dummy text of the printing and typesetting industry. Ipsum has been.</p>
  </div>
  <div class="abs service" style="left:872px">
    <div class="icon"><svg viewBox="0 0 52 52"><circle cx="26" cy="22" r="11" fill="#000"/><rect x="21" y="32" width="10" height="5" fill="#000"/><rect x="22" y="39" width="8" height="3" fill="#000"/></svg></div>
    <h3>IDEATION</h3><p>Lorem Ipsum is simply dummy text of the printing and typesetting industry. Ipsum has been.</p>
  </div>
  <div class="abs btn">View All <svg viewBox="0 0 32 32"><circle cx="16" cy="16" r="13" fill="none" stroke="#fff" stroke-width="2.5"/><path d="M11 16h10M17 11l5 5-5 5" fill="none" stroke="#fff" stroke-width="2.5"/></svg></div>
</section>

<div class="abs ring"></div>
<div class="abs ring-inner"></div>
<div class="abs ring-line"></div>
<div class="abs typewriter" role="img" aria-label="Photo of a vintage black typewriter with a blank sheet of paper"></div>

<h2 class="abs section-title" style="top:2062px">Some of Our Successful Projects</h2>
<p class="abs lede projects-sub">Lorem Ipsum is simply dummy text of the printing and typesetting industry.</p>
<div class="abs grid">
  <div class="tile" role="img" aria-label="Project photo: person looking through binoculars"></div>
  <div class="tile" role="img" aria-label="Project photo: laptop and coffee on a wooden table"></div>
  <div class="tile" role="img" aria-label="Project photo: laptop, notes and photos on a desk"></div>
  <div class="tile" role="img" aria-label="Project photo: hands with a phone and laptop"></div>
  <div class="tile" role="img" aria-label="Project photo: open notebook on a desk"></div>
  <div class="tile" role="img" aria-label="Project photo: chalk arrows on pavement"></div>
  <div class="tile" role="img" aria-label="Project photo: dark typewriter close-up"></div>
  <div class="tile" role="img" aria-label="Project photo: hands typing on a laptop"></div>
</div>
<div class="abs viewall-band"><div class="btn">View All <svg viewBox="0 0 32 32"><circle cx="16" cy="16" r="13" fill="none" stroke="#fff" stroke-width="2.5"/><path d="M11 16h10M17 11l5 5-5 5" fill="none" stroke="#fff" stroke-width="2.5"/></svg></div></div>

<h2 class="abs section-title" style="top:2796px">Latest Blog</h2>
<article class="abs post" style="left:77px">
  <div class="abs thumb" role="img" aria-label="Blog photo: people working in a cafe" style="background:linear-gradient(135deg,#5a4632,#b78a58)"></div>
  <div class="abs date"><b>30</b><small>Aug</small></div>
  <div class="abs body"><h4>Lorem Ipsum is the simply dummy text of print.</h4><p>Lorem Ipsum is simply dummy text of the printing and typesetting industry. Ipsum has been Ipsum is simply text of the printing and typesetting..</p><a class="more">Read More...»</a></div>
</article>
<article class="abs post" style="left:629px">
  <div class="abs thumb" role="img" aria-label="Blog photo: man working on a laptop" style="background:linear-gradient(135deg,#3a3f46,#9aa0a6)"></div>
  <div class="abs date"><b>30</b><small>Aug</small></div>
  <div class="abs body"><h4>Lorem Ipsum is the simply dummy text of print.</h4><p>Lorem Ipsum is simply dummy text of the printing and typesetting industry. Ipsum has been Ipsum is simply text of the printing and typesetting..</p><a class="more">Read More...»</a></div>
</article>

<footer class="abs footer">
  <div class="abs brand"><i class="mark"></i><div>Mara Penrith<small>COPYWRITER</small></div></div>
  <div class="abs social">
    <a class="social-link" aria-label="Share"><svg viewBox="0 0 20 20"><circle cx="5" cy="10" r="2.6" fill="#000"/><circle cx="15" cy="4.5" r="2.6" fill="#000"/><circle cx="15" cy="15.5" r="2.6" fill="#000"/><path d="M5 10l10-5.5M5 10l10 5.5" stroke="#000" stroke-width="1.8"/></svg></a>
    <a class="social-link" aria-label="Link"><svg viewBox="0 0 20 20"><rect x="1.5" y="7" width="10" height="6" rx="3" fill="none" stroke="#000" stroke-width="2"/><rect x="8.5" y="7" width="10" height="6" rx="3" fill="none" stroke="#000" stroke-width="2"/></svg></a>
    <a class="social-link" aria-label="Message"><svg viewBox="0 0 20 20"><path d="M3 4h14v9H8l-4 3v-3H3z" fill="#000"/></svg></a>
  </div>
  <div class="abs col sitemap" style="left:345px"><h5>Sitemap</h5><ul><li>Home</li><li>Services</li><li>Portfolio</li><li>Blog</li><li>Contact</li></ul></div>
  <div class="abs col" style="left:608px"><h5>Contact Us</h5>
    <div class="contact-list">
      <div><svg viewBox="0 0 18 18"><path d="M9 1a6 6 0 0 1 6 6c0 5-6 10-6 10S3 12 3 7a6 6 0 0 1 6-6z" fill="#cfcfcf"/><circle cx="9" cy="7" r="2" fill="#141414"/></svg>101 - Lorem ipsum simple text of print and type.</div>
      <div><svg viewBox="0 0 18 18"><path d="M4 2l3 3-2 2c1 2 3 4 5 5l2-2 3 3-2 2C7 15 2 10 2 4z" fill="#cfcfcf"/></svg>0412 583 906</div>
      <div style="word-break:break-all"><svg viewBox="0 0 18 18"><rect x="2" y="4" width="14" height="10" fill="#cfcfcf"/><path d="M2 4l7 6 7-6" stroke="#141414" fill="none"/></svg>mara.penrith.copywriter@fernmail.test</div>
    </div>
  </div>
  <div class="abs col newsletter" style="left:874px"><h5>Newsletter</h5>
    <p>Would you like to receive our exclusive news and update please sign up for newsletter</p>
    <div class="subscribe"><span>Enter Email *</span><b><svg viewBox="0 0 20 20"><path d="M2 10l16-7-5 15-3-6z" fill="#fff"/></svg></b></div>
  </div>
</footer>
<div class="abs copyright"><b>©mara penrith copywriter</b> - 2018 All Right Reserved.</div>

</body>
</html>
```